BRAMBLEFORD CONSTRUCTIONS B-Card

I currently have a b-card design but will be removing the image (tree) from the logo and have text only.
I want the card to be classy and strong within the building and construction industry.
I will be using Spot UV on the cards as per the attached examples. I will also send through some sketched ideas that I have in mind.
The color blue is similar to the image (No. 6) attached images

Target Market(s)

middle to maturre aged.
Home Owners / Renovators and Builders

Industry/Entity Type

Construction

Contact Information for Business Card

BRAMBLEFORD CONSTRUCTIONS
Name: Gareth Pennick
Title: Project Manager
Mobile: 0427 351 804
Office: (08) 9316 5172
Address: 47C Corvell Street, Malaga WA 6090
Email: info@bramblefordhomes.com.au
PO Box: 3817 Malaga WA 6944

Colors
0592cd
33a6d7
85cae6
1b1b1b

Requirements
Must have
• 1. It must have spot UV on the front of card, maybe back of card too
• 2. I really like the blue on image 6. (or at least a really cool electric blue against the charcoal grey background)
• 3. The font must be slimline and modern. Easy to read
• 4. There must be no black used on the card... Only greys and dark charcoal greys
• 5. Use only the text from the logo "Brambleford Constructions" Not the image of the tree. I am wanting the b-cards to be more masculine.
Nice to have
• 1. I like the design concept on image 6. but happy to see what else you can do with the Spot UV
• 2. Unless you have a really cool idea of the image of the tree (from previous logo) Spot UV somewhere in the design concept thats original and different then I am keen to see what you come up with
• 3. Try changing the color of the logo eg. full white or Blue and white
• 4. Another option is to have the Brambleford Logo on the front of card with the spot UV in the background of text which we specialise in eg, Roofing, Ceiling, Insulation, Gutter Guards, Electrical, Insurance etc and we can add or reduce items as required. Similar to image 12.
Should not have
• Do not include the image of the tree from previous logo. unless you have a really cool idea of Spot UV somewhere in the design concept thats original and different.

```html
<!DOCTYPE html>
<html lang="en">
<head>
<meta charset="utf-8">
<title>Brambleford Constructions – Business Card</title>
<link rel="stylesheet" href="https://fonts.googleapis.com/css2?family=Jost:wght@400;500;600&display=swap">
<style>
  :root {
    --stage: #d9dadc;
    --card: #1b1b1b;
    --card-deep: #151617;
    --pattern-light: #2a2b2e;
    --blue: #1f6fc4;
    --text: #e9e9ea;
    --muted: #c8c9cb;
    --white: #ffffff;
  }
  * { box-sizing: border-box; margin: 0; padding: 0; }
  html, body { width: 1200px; height: 747px; overflow: hidden; }
  body {
    background: var(--stage);
    font-family: "Jost", sans-serif;
    color: var(--text);
  }
  .canvas {
    position: relative;
    width: 1200px;
    height: 747px;
    display: flex;
    align-items: center;
    justify-content: center;
    gap: 40px;
  }
  .card {
    position: relative;
    width: 540px;
    height: 310px;
    border-radius: 18px;
    background: var(--card);
    overflow: hidden;
    box-shadow: 0 10px 24px rgba(40, 40, 45, 0.25);
  }

  /* Back */
  .card-back .spot-uv-field {
    position: absolute;
    inset: 0;
    background: linear-gradient(135deg, var(--card-deep) 0%, var(--pattern-light) 50%, var(--card-deep) 100%);
  }
  .services {
    position: absolute;
    left: 0; right: 0;
    top: 50%;
    transform: translateY(-50%);
    text-align: center;
    font-size: 14px;
    line-height: 1.35;
    letter-spacing: 0.02em;
    color: var(--text);
  }

  /* Front */
  .brand {
    position: absolute;
    left: 40px;
    top: 38px;
    color: var(--blue);
    font-size: 26px;
    font-weight: 500;
    line-height: 1.1;
    letter-spacing: 0;
  }

  .address {
    position: absolute;
    left: 40px;
    top: 100px;
    font-size: 15px;
    line-height: 1.2;
    font-style: normal;
    color: var(--muted);
  }
  .address p + p { margin-top: 8px; }

  .contact {
    position: absolute;
    left: 40px;
    top: 196px;
    list-style: none;
    font-size: 15px;
    line-height: 1.45;
    color: var(--muted);
  }
  .contact li { display: flex; align-items: center; gap: 8px; }
  .contact svg { width: 14px; height: 14px; fill: var(--blue); flex: none; }

  .name-band {
    position: absolute;
    right: 0;
    bottom: 40px;
    width: 230px;
    height: 58px;
    background: var(--blue);
    clip-path: polygon(22px 0, 100% 0, 100% 100%, 0 100%);
    padding: 8px 22px 0 0;
    text-align: right;
    color: var(--white);
  }
  .person-name { font-size: 21px; font-weight: 600; line-height: 1.1; }
  .person-title { font-size: 16px; font-weight: 400; line-height: 1.2; }
</style>
</head>
<body>
<main class="canvas">

  <section class="card card-back" aria-label="Business card back">
    <div class="spot-uv-field" role="img" aria-label="Spot UV pattern of repeated company name across the card"></div>
    <p class="services">Roofing | Ceiling | Insulation | Gutter Guards<br>Electrical | Insurance etc</p>
  </section>

  <section class="card card-front" aria-label="Business card front">
    <h1 class="brand">Brambleford Constructions</h1>

    <address class="address">
      <p>47C Corvell Street<br>Malaga WA 6090</p>
      <p>PO Box:<br>3817 Malaga WA 6944</p>
    </address>

    <ul class="contact">
      <li>
        <svg viewBox="0 0 24 24" aria-hidden="true"><path d="M6.6 10.8a15.1 15.1 0 0 0 6.6 6.6l2.2-2.2a1 1 0 0 1 1-.25 11.4 11.4 0 0 0 3.6.57 1 1 0 0 1 1 1V20a1 1 0 0 1-1 1A17 17 0 0 1 3 4a1 1 0 0 1 1-1h3.5a1 1 0 0 1 1 1c0 1.25.2 2.450.57 3.57a1 1 0 0 1-.25 1z"/></svg>
        (08) 9316 5172
      </li>
      <li>
        <svg viewBox="0 0 24 24" aria-hidden="true"><path d="M7 1h10a2 2 0 0 1 2 2v18a2 2 0 0 1-2 2H7a2 2 0 0 1-2-2V3a2 2 0 0 1 2-2zm0 3v14h10V4zm5 15.5a1.2 1.2 0 1 0 0 2.4 1.2 1.2 0 0 0 0-2.4z"/></svg>
        0427 351 804
      </li>
      <li>
        <svg viewBox="0 0 24 24" aria-hidden="true"><path d="M2 5h20v14H2zm2 2v.4l8 5.3 8-5.3V7zm0 2.8V17h16V9.8l-8 5.3z"/></svg>
        info@bramblefordhomes.com.au
      </li>
    </ul>

    <div class="name-band">
      <p class="person-name">Gareth Pennick</p>
      <p class="person-title">Project Manager</p>
    </div>
  </section>

</main>
</body>
</html>
```